Vellmore Family Law, legal technician needs a website and design

I need a website for a family law practice. I specialize in collaborative law, unbundled services, and mediation. The website must contain my company logo (file attached), and the website must be a mixture of my personality and my profession. I have attached additional information to explain my personality and profession.

Target Market(s)

Lower through middle-class (income level up to $200,000 per year)

Coding

Coded - Design and coding required

Number of Pages Required

1 page

Requirements
Must have
• Must have enough pages to cover required content. I submitted below some content about the collaborative law process. All of the content is not necessary. However, the website must have enough content to clearly describe the services I offer. Use your professionalism and judgment regarding font, font size, etc.

```html
<!DOCTYPE html>
<html lang="en">
<head>
<meta charset="utf-8">
<title>Vellmore Family Law</title>
<link rel="stylesheet" href="https://fonts.googleapis.com/css2?family=Cinzel:wght@600;700&family=Montserrat:wght@400;500;600;700&display=swap">
<style>
:root{
  --navy:#0d0c3d;
  --navy-deep:#090833;
  --gold:#b9b03c;
  --gold-dark:#8c7f2c;
  --gold-grad:linear-gradient(180deg,#bdb63e 0%,#8f832e 100%);
  --light:#f6f6f7;
  --text:#3a3a48;
  --white:#ffffff;
}
*{margin:0;padding:0;box-sizing:border-box}
html,body{width:1200px;height:4255px;overflow:hidden}
body{font-family:'Montserrat',sans-serif;color:var(--text);background:var(--white);position:relative}
.serif{font-family:'Cinzel',serif}
section,header,footer,div{position:relative}
.abs{position:absolute}

.topbar{height:61px;background:var(--navy-deep);color:var(--white);font-size:13px;font-weight:500;text-align:center;line-height:61px}

.hero{height:1108px;background:var(--navy)}
.hero-photo{position:absolute;left:0;top:0;width:1200px;height:800px;background:linear-gradient(180deg,#f2f1ee 0%,#d9d3c8 25%,#9b8e80 55%,#3c3650 80%,#0d0c3d 100%)}
.site-header{position:absolute;left:172px;top:28px;width:856px;height:60px;display:flex;align-items:center}
.brand{display:flex;align-items:center;gap:10px;font-family:'Cinzel',serif;font-weight:700;font-size:22px;color:var(--gold-dark);width:250px}
.brand-mark{width:18px;height:18px;background:var(--gold)}
.nav{display:flex;gap:19px;font-size:13px;font-weight:500;color:var(--navy);margin-left:0}
.phone-btn{margin-left:auto;background:var(--gold-grad);color:var(--white);font-weight:700;font-size:15px;height:60px;width:168px;display:flex;align-items:center;justify-content:center;gap:6px}
.hero-band{position:absolute;left:215px;top:537px;width:770px;height:93px;background:linear-gradient(90deg,rgba(185,176,60,0) 0%,rgba(185,176,60,.95) 20%,rgba(185,176,60,.95) 80%,rgba(185,176,60,0) 100%);display:flex;align-items:center;justify-content:center;color:var(--white);font-family:'Cinzel',serif;font-weight:700;font-size:45px;letter-spacing:1px}
.features{position:absolute;left:172px;top:893px;width:856px;display:flex;justify-content:space-between}
.feature{width:254px;height:125px;border:2px solid var(--gold);display:flex;padding:30px 14px 0 16px;gap:14px;color:var(--white)}
.feature h3{font-size:13px;font-weight:600;margin-bottom:12px}
.feature p{font-size:12px;line-height:21px;color:#d8d8e4}

.section-title{font-family:'Cinzel',serif;font-weight:700;font-size:34px;color:var(--navy);text-align:center;letter-spacing:.5px}
.title-rule{width:92px;height:2px;background:var(--gold);margin:14px auto 0}

.what{height:1162px;background:var(--light);padding-top:76px}
.video{position:absolute;left:173px;top:186px;width:854px;height:435px;background:linear-gradient(135deg,#6f6058 0%,#a8968a 40%,#d7cfc8 65%,#5d5460 100%)}
.play{position:absolute;left:399px;top:189px;width:56px;height:56px;border-radius:50%;background:var(--white)}
.play:after{content:"";position:absolute;left:22px;top:17px;border-left:17px solid var(--navy);border-top:11px solid transparent;border-bottom:11px solid transparent}
.how{position:absolute;left:173px;top:718px;width:500px}
.how h2{font-family:'Cinzel',serif;font-weight:700;font-size:33px;color:var(--navy)}
.how .rule{width:92px;height:2px;background:var(--gold);margin:14px 0 24px}
.how p{font-size:11.6px;line-height:22.5px;text-align:justify}
.btn{display:inline-flex;align-items:center;justify-content:center;font-weight:700;font-size:15px;color:var(--white);background:var(--gold-grad);letter-spacing:.5px}
.how .btn{width:139px;height:59px;margin-top:24px}
.name-deco{position:absolute;left:711px;top:800px;width:317px;display:flex;align-items:center;gap:14px;font-family:'Cinzel',serif;font-weight:700;font-size:44px;color:var(--gold);line-height:1.1}
.name-deco .sq{width:30px;height:30px;background:var(--gold);flex:none}

.benefits{height:558px;background:linear-gradient(180deg,#2a2a5c 0%,#1a1950 40%,var(--navy) 100%);padding-top:80px}
.benefits .section-title{color:var(--gold)}
.cards{position:absolute;left:172px;top:210px;width:856px;display:flex;justify-content:space-between}
.benefit{width:264px;height:241px;border:2px solid var(--gold);text-align:center;color:var(--white);padding-top:30px}
.benefit.active{background:var(--gold-grad);border-color:var(--gold)}
.benefit svg{margin:0 auto}
.benefit h3{font-size:17px;font-weight:600;margin:20px 0 18px}
.benefit p{font-size:11.5px;line-height:21px;color:#d8d8e4;padding:0 24px}
.benefit.active p{color:#f2f0d8}

.blog{height:752px;background:var(--white);padding-top:78px}
.posts{position:absolute;left:172px;top:191px;width:856px;display:flex;justify-content:space-between}
.post{width:264px;height:441px;background:var(--white);box-shadow:0 2px 14px rgba(0,0,0,.12)}
.post-img{height:206px}
.post-body{padding:20px 17px}
.meta{font-size:11px;display:flex;gap:14px;color:#555}
.post h3{font-size:15px;font-weight:700;color:var(--navy);margin:18px 0 12px;letter-spacing:.3px}
.post p{font-size:11px;line-height:19.5px;text-align:justify}
.post .btn{font-size:11px;height:38px;width:96px;margin-top:14px;background:var(--navy)}
.post .btn.gold{background:var(--gold-grad)}

.cta{height:103px;background:linear-gradient(180deg,#bcb43e,#918530);display:flex;align-items:center;padding:0 172px}
.cta p{color:var(--white);font-size:17px;font-weight:600;line-height:27px;width:560px}
.cta .b{height:55px;display:flex;align-items:center;justify-content:center;font-size:14px;font-weight:700;letter-spacing:.5px}
.cta .next{margin-left:auto;width:131px;background:var(--white);color:var(--gold-dark)}
.cta .contact{width:128px;background:var(--navy);color:var(--white);margin-left:13px}

.footer{height:511px;background:var(--navy);color:var(--white)}
.f-brand{position:absolute;left:173px;top:110px;display:flex;align-items:center;gap:12px;font-family:'Cinzel',serif;font-weight:700;font-size:26px;color:var(--gold)}
.f-brand .sq{width:22px;height:22px;background:var(--gold)}
.field{position:absolute;top:207px;height:43px;border:2px solid var(--white);font-size:12px;padding:12px 10px}
.submit{position:absolute;left:173px;top:266px;width:97px;height:43px;font-size:15px;font-weight:500}
.f-col{position:absolute;top:96px}
.f-col h4{font-size:15px;font-weight:700;letter-spacing:.5px;margin-bottom:22px}
.links li{list-style:none;font-size:13.5px;margin-bottom:13px}
.c-row{display:flex;gap:14px;margin-bottom:24px;font-size:13px;font-weight:600;line-height:23px}
.c-ic{width:41px;height:41px;border-radius:50%;background:var(--gold);flex:none;display:flex;align-items:center;justify-content:center}
.f-rule{position:absolute;left:173px;top:405px;width:854px;height:2px;background:var(--gold)}
.copy{position:absolute;left:172px;top:448px;font-size:13px}
.social{position:absolute;left:818px;top:442px;display:flex;gap:18px}
.social span{width:28px;height:28px;border-radius:50%;background:var(--gold)}
.chat{position:absolute;right:0;top:3858px;width:66px;height:228px;background:var(--gold-grad);color:var(--white);display:flex;flex-direction:column;align-items:center;justify-content:flex-end;padding-bottom:20px;gap:14px}
.chat span{writing-mode:vertical-rl;transform:rotate(180deg);font-size:24px;font-weight:600}
</style>
</head>
<body>

<div class="topbar">Vellmore Family Law, collaborative law and unbundled legal services in King County, Washington state</div>

<section class="hero">
  <div class="hero-photo" role="img" aria-label="Family of three meeting with a lawyer at an office table"></div>
  <header class="site-header">
    <div class="brand"><span class="brand-mark"></span>Vellmore</div>
    <nav class="nav"><span>Home</span><span>About</span><span>Our Attorney</span><span>Case Study</span><span>Blog</span><span>Contact</span></nav>
    <div class="phone-btn">
      <svg width="16" height="16" viewBox="0 0 24 24" fill="none" stroke="#fff" stroke-width="2"><path d="M5 3h4l2 5-3 2a11 11 0 0 0 6 6l2-3 5 2v4a2 2 0 0 1-2 2A17 17 0 0 1 3 5a2 2 0 0 1 2-2z"/></svg>
      + 123 456 7890
    </div>
  </header>
  <div class="hero-band">VELLMORE FAMILY LAW</div>
  <div class="features">
    <div class="feature">
      <svg width="40" height="40" viewBox="0 0 40 40" fill="none" stroke="#b9b03c" stroke-width="2"><path d="M12 5h16v10a8 8 0 0 1-16 0z"/><path d="M12 8H6c0 6 3 9 6 9M28 8h6c0 6-3 9-6 9M20 23v7M13 35h14"/></svg>
      <div><h3>99% Winning Guarantee</h3><p>Lorem ipsum dolor sit amet, con sectetu adipiscing</p></div>
    </div>
    <div class="feature">
      <svg width="40" height="40" viewBox="0 0 40 40" fill="none" stroke="#b9b03c" stroke-width="2"><path d="M20 4l13 5v10c0 9-6 15-13 18C13 34 7 28 7 19V9z"/><path d="M14 20l5 5 8-9"/></svg>
      <div><h3>Secure Management</h3><p>Lorem ipsum dolor sit amet, con sectetu adipiscing</p></div>
    </div>
    <div class="feature">
      <svg width="40" height="40" viewBox="0 0 40 40" fill="none" stroke="#b9b03c" stroke-width="2"><path d="M7 22v-4a13 13 0 0 1 26 0v4"/><rect x="4" y="20" width="6" height="10" rx="2"/><rect x="30" y="20" width="6" height="10" rx="2"/><path d="M33 30c0 4-5 6-11 6"/></svg>
      <div><h3>Full Time Support</h3><p>Lorem ipsum dolor sit amet, con sectetu adipiscing</p></div>
    </div>
  </div>
</section>

<section class="what">
  <h2 class="section-title">WHAT I DO</h2>
  <div class="title-rule"></div>
  <div class="video" role="img" aria-label="Video still of a family signing documents with their lawyer"><span class="play"></span></div>
  <div class="how">
    <h2>HOW I DO IT</h2>
    <div class="rule"></div>
    <p>Even with these differences all these people have one thing in common: A trust that through the Collaborative Process the result of their divorce or legal is going to be better than it would be in any other process they could choose. It is this trust that is the guiding force of the process, not the law, not the lawyers or other pro fessionals on the Collaborative Team. When the trust is strong the process runs more smoothly. When the trust is diluted, the process can be like walking in deep mud, something akin to a slog.</p>
    <span class="btn">READ MORE</span>
  </div>
  <div class="name-deco"><span class="sq"></span>Vellmore</div>
</section>

<section class="benefits">
  <h2 class="section-title">BENEFITS OF WHAT I DO</h2>
  <div class="title-rule"></div>
  <div class="cards">
    <div class="benefit">
      <svg width="58" height="58" viewBox="0 0 58 58" fill="none" stroke="#b9b03c" stroke-width="2"><path d="M29 6v46M18 52h22M10 16h38M29 10a3 3 0 1 0 0 .1"/><path d="M14 16l-6 16h12zM44 16l-6 16h12z"/></svg>
      <h3>Family Law</h3>
      <p>Simply trusting in the process, how ever, is not enough. The process of divorcing.</p>
    </div>
    <div class="benefit active">
      <svg width="58" height="58" viewBox="0 0 58 58" fill="none" stroke="#fff" stroke-width="2"><rect x="14" y="6" width="30" height="44" rx="2"/><path d="M14 12h30M26 22c0-4 8-4 8 0s-8 4-8 8 8 4 8 0"/></svg>
      <h3>Collaborative Law</h3>
      <p>Collaborate practice is a process where trained professionals, includ ing attorneys.</p>
    </div>
    <div class="benefit">
      <svg width="58" height="58" viewBox="0 0 58 58" fill="none" stroke="#b9b03c" stroke-width="2"><path d="M29 6l18 6v14c0 12-8 20-18 25-10-5-18-13-18-25V12z"/><path d="M29 18l3 7h7l-6 4 2 7-6-4-6 4 2-7-6-4h7z"/></svg>
      <h3>Mediation Law</h3>
      <p>If you want one partner to keep the house, or you want to wait to sell the house to time the market.</p>
    </div>
  </div>
</section>

<section class="blog">
  <h2 class="section-title">LATEST BLOG POST</h2>
  <div class="title-rule"></div>
  <div class="posts">
    <article class="post">
      <div class="post-img" role="img" aria-label="Colleagues talking at a meeting table" style="background:linear-gradient(135deg,#d9d6cf,#7d7066 55%,#3a3f52)"></div>
      <div class="post-body">
        <div class="meta"><span>Apr 18, 2021</span><span>Mara Ellison</span></div>
        <h3>NAM LIBERO TEMPORE</h3>
        <p>At vero eos et accusamus et iusto odio dignissimos ducimus qui blanditiis praesentium.</p>
        <span class="btn">READ MORE</span>
      </div>
    </article>
    <article class="post">
      <div class="post-img" role="img" aria-label="Business team reviewing papers in an office" style="background:linear-gradient(135deg,#8c7a5d,#c9bba4 50%,#4a4a52)"></div>
      <div class="post-body">
        <div class="meta"><span>Apr 18, 2021</span><span>Mara Ellison</span></div>
        <h3>NAM LIBERO TEMPORE</h3>
        <p>At vero eos et accusamus et iusto odio dignissimos ducimus qui blanditiis praesentium.</p>
        <span class="btn gold">READ MORE</span>
      </div>
    </article>
    <article class="post">
      <div class="post-img" role="img" aria-label="Professionals in discussion at a bright office table" style="background:linear-gradient(135deg,#e6e7ea,#8e99a8 50%,#2f3a5a)"></div>
      <div class="post-body">
        <div class="meta"><span>Apr 18, 2021</span><span>Mara Ellison</span></div>
        <h3>NAM LIBERO TEMPORE</h3>
        <p>At vero eos et accusamus et iusto odio dignissimos ducimus qui blanditiis praesentium.</p>
        <span class="btn">READ MORE</span>
      </div>
    </article>
  </div>
</section>

<section class="cta">
  <p>Vellmore Family Law, collaborative law and unbundled legal services in King County, Washington state</p>
  <span class="b next">NEXT STEP</span>
  <span class="b contact">CONTACT US</span>
</section>

<footer class="footer">
  <div class="f-brand"><span class="sq"></span>Vellmore</div>
  <div class="field" style="left:173px;width:151px">Name</div>
  <div class="field" style="left:332px;width:149px">Phone</div>
  <span class="btn submit">SUBMIT</span>
  <div class="f-col" style="left:550px">
    <h4>QUICK LINKS</h4>
    <ul class="links"><li>Home</li><li>About</li><li>Our Attorney</li><li>Case Study</li><li>Blog</li><li>Contact</li></ul>
  </div>
  <div class="f-col" style="left:755px">
    <h4>CONTACT US</h4>
    <div class="c-row"><span class="c-ic"><svg width="18" height="18" viewBox="0 0 24 24" fill="none" stroke="#fff" stroke-width="2"><path d="M5 3h4l2 5-3 2a11 11 0 0 0 6 6l2-3 5 2v4a2 2 0 0 1-2 2A17 17 0 0 1 3 5a2 2 0 0 1 2-2z"/></svg></span><div>Phone:<br>+ 123 456 7890</div></div>
    <div class="c-row"><span class="c-ic"><svg width="18" height="18" viewBox="0 0 24 24" fill="none" stroke="#fff" stroke-width="2"><rect x="3" y="5" width="18" height="14"/><path d="M3 6l9 7 9-7"/></svg></span><div>Mail:<br>info@vellmorefamilylaw</div></div>
    <div class="c-row"><span class="c-ic"><svg width="18" height="18" viewBox="0 0 24 24" fill="none" stroke="#fff" stroke-width="2"><path d="M12 22s7-7 7-12a7 7 0 0 0-14 0c0 5 7 12 7 12z"/><circle cx="12" cy="10" r="2.5"/></svg></span><div>Address:<br>58 Harlow Lane, Brenton<br>WA 98012, USA</div></div>
  </div>
  <div class="f-rule"></div>
  <div class="copy">Copyrights @ 2021 Vellmore Family Law. All Rights Reserved.</div>
  <div class="social"><span></span><span></span><span></span><span></span><span></span></div>
</footer>

<div class="chat">
  <span>Live chat</span>
  <svg width="26" height="26" viewBox="0 0 24 24" fill="none" stroke="#fff" stroke-width="2"><rect x="3" y="4" width="18" height="14" rx="2"/><path d="M8 18v4l4-4"/></svg>
</div>

</body>
</html>
```